Doctor Formulated Medical Cosmetics

Velour Skinhaus is an E-commerce site for high end Medical Cosmetics designed to treat specific skin problems. The Velour Skinhaus difference/advantage is that all creams and serums are:
Doctor Formulated, Freshly Handmade, Registered Pharmacy.
The Site also provides real doctor Dermatology Consultations, Library (with a list of - 1. Active Ingredients in the creams with description of their effects, 2. Skin Conditions with information on what causes the condition and typical treatment approaches and outcomes. 3. Resources from Dermatology Journals and literature on the conditions.)
Header Information: Velour Skinhaus, languages EN, BG, Register / log in, Shopping Bag. This field should be narrow.
Categories (horizontal): Home, Face, Body, Hair Care, Skin Conditions, Doctor Consultation, Library
The Landing Page should have only one well organized picture, which is intended to create the feeling of luxury, freedom and relaxation. It will be large and will fill the whole screen. All text should be on transparent or similar color fields. Please use the color of the text to create also the feeling of conservative luxury.
Written message / image overlay Velour Skinhaus(logo), Skin Care, Doctor Formulated, Freshly Handmade, Registered Pharmacy.
Please study the Landing Page of this site as an example: www.marivane.com
Under the Landing Page, there should be a slider with 4 of our products.
Underneath: Four Blog Articles (large pictures for maximum impact and luxury text underneath).
Underneath: Banner for Dermatologist Consultation, (button for Start Your Case Now).
Underneath: Two pictures in a line - Library (with books), and Active Ingredients.
Footer: Philosophy, Categories, Customer Care
Please adhere to the color palate provided in the pictures (as attachments). Provided are some examples of Web Sites with the desired look and feel. www.quillora.com , www.tavenholtmd.com .
Please use different shades of gray, white, beige and gold colors, and black. Our products will be in brown glass jars and bottles to convey the professional, pharmacy made nature of the creams and lotions.
We find the following Front Page very attractive and effective - www.marivane.com , with its full page image and overlaying text.
Please have a look at this link for the Landing page.
http://www.brimlensphoto.com/detail/video/woman-lying-on-a-black-sand-beach-in-a-bikini-stock-footage/58213067
I would like to use it in the animated version to achieve the WOW effect. I have uploaded the jpeg version for it, so you will be able create your design.
For the Landing page design, please use only the two uploaded pictures of a woman laying at the beach. Let's see how each of them will look like.
Thank you for your help.

```html
<!DOCTYPE html>
<html lang="en">
<head>
<meta charset="utf-8">
<title>Velour Skinhaus</title>
<link href="https://fonts.googleapis.com/css2?family=Marcellus+SC&family=Lato:ital,wght@0,400;0,700;1,400&display=swap" rel="stylesheet">
<style>
:root{
  --gold:#d3b16b;
  --gold-band:#d8b870;
  --ink:#1e1e1e;
  --text:#333;
  --topbar:#2a2a2a;
  --footer:#141414;
  --line:#d9c59a;
  --card-border:#d8d8d8;
  --white:#fff;
}
*{box-sizing:border-box;margin:0;padding:0}
html,body{width:1200px;height:2462px;overflow:hidden}
body{position:relative;background:var(--white);font-family:'Lato',Arial,sans-serif;color:var(--text)}
.abs{position:absolute}
svg{display:block}
h1,h2,h3,h4{font-weight:400}

/* header */
.topbar{left:476px;top:0;width:662px;height:40px;background:var(--topbar);border-radius:0 0 30px 30px;display:flex;align-items:center;justify-content:space-around;padding:0 40px;color:#eee;font-size:13px}
.topbar span{display:flex;align-items:center;gap:6px}
.flag{width:20px;height:13px;background:#3a4f8f;border:1px solid #999}
.brand{left:59px;top:36px;display:flex;align-items:center;gap:14px;font-size:40px;color:var(--gold)}
.brand-dot{width:52px;height:52px;border:3px solid var(--gold);border-radius:50%}
.contact-head{top:58px;display:flex;align-items:center;gap:10px;font-size:15px;color:#333;line-height:1.3}
.contact-head svg{width:38px;height:38px}

/* nav */
.nav{left:0;top:125px;width:1200px;height:49px;background:var(--gold-band);display:flex;justify-content:center}
.nav ul{list-style:none;display:flex;width:1082px;border-left:1px solid #c9a55a}
.nav li{border-right:1px solid #c9a55a;display:flex;align-items:center;justify-content:center;font-size:14px;color:#2a2a2a;font-weight:700}

/* hero */
.hero{left:0;top:174px;width:1200px;height:443px;background:
  radial-gradient(ellipse 300px 360px at 1020px 260px,#f0d2c4 0%,#e6bcaa 40%,rgba(230,188,170,0) 75%),
  radial-gradient(ellipse 260px 140px at 820px 30px,#f6e2ee 0%,rgba(246,226,238,0) 70%),
  radial-gradient(ellipse 200px 200px at 1160px 100px,#6e4a3a 0%,rgba(110,74,58,0) 70%),
  linear-gradient(90deg,#f3f1f4 0%,#eeeaf0 45%,#e8dfe6 65%,#e6d4d2 100%)}
.hero-title{left:57px;top:244px;font-family:'Marcellus SC',serif;font-size:42px;color:#1a1a1a;letter-spacing:2px}
.advantages{left:59px;top:318px;list-style:none}
.advantages li{display:flex;align-items:center;gap:14px;font-size:23px;color:#222;height:54px}
.hero-ring{left:513px;top:295px;width:220px;height:220px;border:2px dotted rgba(211,177,107,.7);border-radius:50%}
.hero-ring::after{content:"";position:absolute;inset:10px;border:2px solid rgba(211,177,107,.45);border-radius:50%}
.dots{left:568px;top:579px;display:flex;gap:8px;align-items:center}
.dots i{width:12px;height:12px;border-radius:50%;background:#222;border:2px solid #fff}
.dots i.on{width:18px;height:18px;background:var(--gold)}

/* section heading */
.sec-head{left:0;width:1200px;text-align:center;font-size:36px;color:#222}
.sec-head em{font-style:normal;color:var(--gold)}
.sec-line{left:59px;width:1079px;height:1px;background:var(--line)}
.sec-notch{left:592px;width:0;height:0;border-left:9px solid transparent;border-right:9px solid transparent;border-top:8px solid #555}

/* products */
.product{top:727px;width:184px;height:279px;border:1px solid var(--card-border);background:#fff;text-align:center}
.product .shot{height:150px;margin:18px auto 0}
.product p{font-size:13px;color:#333;line-height:1.6;margin-top:16px}
.price{display:flex;align-items:center;justify-content:center;gap:8px;margin-top:6px;font-weight:700;font-size:15px;color:#222}
.cart{width:34px;height:34px;border-radius:50%;background:var(--gold);display:flex;align-items:center;justify-content:center}
.arrow{top:816px;width:37px;height:54px;display:flex;align-items:center;justify-content:center}
.arrow.prev{left:61px;background:#e4e4e4}
.arrow.next{left:1101px;background:#2b2b2b}
.deco-right{left:1000px;top:617px;width:200px;height:430px;background:
  radial-gradient(ellipse 120px 100px at 150px 330px,#f6f5ec 0%,rgba(246,245,236,0) 80%),
  radial-gradient(ellipse 110px 160px at 120px 160px,#e4e8c4 0%,rgba(228,232,196,0) 80%),
  linear-gradient(90deg,rgba(255,255,255,1),rgba(255,255,255,0) 40%)}

/* consultation */
.consult{left:0;top:1074px;width:1200px;height:461px;background:
  radial-gradient(ellipse 150px 240px at 110px 300px,#8d8d8f 0%,rgba(141,141,143,0) 80%),
  radial-gradient(ellipse 140px 200px at 380px 320px,#f6f6f6 0%,rgba(246,246,246,0) 80%),
  radial-gradient(ellipse 80px 90px at 110px 110px,#c7a77c 0%,rgba(199,167,124,0) 80%),
  radial-gradient(ellipse 80px 90px at 390px 120px,#b78e64 0%,rgba(183,142,100,0) 80%),
  linear-gradient(90deg,#d8d3cc 0%,#e3e4e6 35%,#cfd5dc 65%,#bcc6cf 100%)}
.consult-title{left:519px;top:1122px;font-size:31px;color:#1a1a1a}
.consult-text{left:519px;top:1172px;width:530px;font-size:14.5px;line-height:1.62;color:#222}
.btn-call{left:520px;top:1347px;width:212px;height:42px;background:var(--gold);border:2px solid #fff;border-radius:6px;display:flex;align-items:center;gap:12px;padding-left:10px;font-size:22px;color:#fff}
.products-group{left:855px;top:1296px;width:300px;height:270px;background:
  radial-gradient(ellipse 150px 140px at 150px 140px,#b8bbc0 0%,#a6a9ae 45%,rgba(170,174,180,0) 85%)}

/* articles */
.article{width:495px;height:173px;border:1px solid var(--card-border);background:#fff}
.article .pic{left:0;top:0;width:164px;height:171px}
.article h3{left:185px;top:18px;font-size:16px;color:var(--gold);font-family:Georgia,serif}
.meta{left:185px;top:51px;display:flex;align-items:center;gap:6px;font-size:12px;color:#222}
.meta span{display:flex;align-items:center;gap:5px;margin-right:12px}
.article p{left:185px;top:80px;width:290px;font-size:14px;line-height:1.35;color:#222}
.read-more{right:-1px;bottom:-1px;width:107px;height:26px;background:var(--gold);color:#fff;font-size:14px;display:flex;align-items:center;justify-content:center;font-weight:700}

/* newsletter */
.newsletter{left:0;top:2104px;width:1200px;height:76px;background:var(--gold-band)}
.nl-icon{left:97px;top:2115px;width:54px;height:54px;border-radius:50%;background:#fff;border:3px solid #222;display:flex;align-items:center;justify-content:center}
.nl-title{left:176px;top:2112px;font-size:23px;color:#fff}
.nl-sub{left:176px;top:2142px;font-size:15px;font-style:italic;color:#fff}
.nl-input{left:541px;top:2122px;width:427px;height:44px;border:1px solid #fff;color:#fff;font-size:12px;font-style:italic;padding:14px}
.nl-btn{left:985px;top:2122px;width:124px;height:44px;background:#fff;color:#222;font-size:13px;font-weight:700;display:flex;align-items:center;justify-content:center}

/* footer */
.footer{left:0;top:2180px;width:1200px;height:282px;background:var(--footer)}
.f-head{top:2210px;font-size:18px;color:#fff}
.f-rule{top:2244px;height:1px;background:#555}
.philosophy{left:62px;top:2256px;width:350px;font-size:13px;line-height:1.6;color:#ddd;text-align:justify}
.links{top:2262px;list-style:none;font-size:14px;line-height:26px;color:#ddd}
.links li::before{content:"› ";color:var(--gold)}
.cinfo{left:900px;display:flex;gap:12px;font-size:13px;color:#ddd;line-height:1.4}
.cinfo b{color:#fff}
.f-bottom{top:2413px;left:0;width:1200px;height:1px;background:#333}
.copyright{left:59px;top:2428px;font-size:12px;color:#ddd}
.social{left:540px;top:2424px;display:flex;gap:8px}
.social i{width:24px;height:24px;border-radius:50%;background:var(--gold)}
.accept{left:855px;top:2426px;display:flex;align-items:center;gap:8px;font-size:12px;color:#ddd}
.accept i{width:36px;height:22px;background:#fff;border-radius:2px}
</style>
</head>
<body>

<div class="abs topbar">
  <span><svg width="14" height="14" viewBox="0 0 14 14"><circle cx="7" cy="5" r="3" fill="none" stroke="#eee" stroke-width="1.5"/><path d="M2 13c0-3 2-4 5-4s5 1 5 4" fill="none" stroke="#eee" stroke-width="1.5"/></svg>Doctor</span>
  <span><svg width="16" height="14" viewBox="0 0 16 14"><rect x="2" y="3" width="12" height="10" rx="1" fill="#eee"/></svg>Pharmacy</span>
  <span><svg width="12" height="14" viewBox="0 0 12 14"><rect x="1" y="6" width="10" height="8" fill="#eee"/><path d="M3 6V4a3 3 0 0 1 6 0v2" fill="none" stroke="#eee" stroke-width="1.5"/></svg>Register / log in</span>
  <span><svg width="16" height="14" viewBox="0 0 16 14"><path d="M0 1h3l2 8h9l2-6H4" fill="none" stroke="#eee" stroke-width="1.5"/><circle cx="6" cy="12" r="1.5" fill="#eee"/><circle cx="13" cy="12" r="1.5" fill="#eee"/></svg>Shopping Cart</span>
  <span><i class="flag"></i>English ⌄</span>
</div>

<div class="abs brand"><span>Velour Skinhaus</span><i class="brand-dot"></i></div>

<div class="abs contact-head" style="left:762px">
  <svg viewBox="0 0 38 38"><path d="M11 6l6 6-3 4c2 4 4 6 8 8l4-3 6 6-4 5C18 32 6 20 6 10z" fill="none" stroke="var(--gold)" stroke-width="2.5"/></svg>
  <div>Call Us:<br>+123-456-789</div>
</div>
<div class="abs contact-head" style="left:935px">
  <svg viewBox="0 0 38 38"><rect x="4" y="10" width="30" height="20" fill="none" stroke="var(--gold)" stroke-width="2.5" transform="rotate(-12 19 20)"/><path d="M5 12l15 10 13-14" fill="none" stroke="var(--gold)" stroke-width="2.5"/></svg>
  <div>Mail Us:<br>info@velourskinhaus.com</div>
</div>

<nav class="abs nav">
  <ul>
    <li style="width:106px">Home</li>
    <li style="width:96px">Face</li>
    <li style="width:96px">Body</li>
    <li style="width:110px">Hair Care</li>
    <li style="width:152px">Skin Concerns</li>
    <li style="width:243px">Dermatologist Consultation</li>
    <li style="width:106px">Library</li>
    <li style="width:173px">Contact Us</li>
  </ul>
</nav>

<div class="abs hero" role="img" aria-label="Close-up of a woman's face with soft floral makeup and pink flowers on a pale lilac background"></div>
<div class="abs hero-ring"></div>
<h1 class="abs hero-title">Product Advantage</h1>
<ul class="abs advantages">
  <li><svg width="30" height="22" viewBox="0 0 30 22"><path d="M2 8h12l-3-5 3-1 8 7v10H6z" fill="none" stroke="var(--gold)" stroke-width="2"/><path d="M14 8h12" stroke="var(--gold)" stroke-width="2"/></svg>Doctor Formulated</li>
  <li><svg width="30" height="22" viewBox="0 0 30 22"><path d="M2 8h12l-3-5 3-1 8 7v10H6z" fill="none" stroke="var(--gold)" stroke-width="2"/><path d="M14 8h12" stroke="var(--gold)" stroke-width="2"/></svg>Freshly Handmade</li>
  <li><svg width="30" height="22" viewBox="0 0 30 22"><path d="M2 8h12l-3-5 3-1 8 7v10H6z" fill="none" stroke="var(--gold)" stroke-width="2"/><path d="M14 8h12" stroke="var(--gold)" stroke-width="2"/></svg>Registered Pharmacy</li>
  <li><svg width="30" height="22" viewBox="0 0 30 22"><path d="M2 8h12l-3-5 3-1 8 7v10H6z" fill="none" stroke="var(--gold)" stroke-width="2"/><path d="M14 8h12" stroke="var(--gold)" stroke-width="2"/></svg>Highest Ethical Standards</li>
</ul>
<div class="abs dots"><i></i><i class="on"></i><i></i></div>

<div class="abs deco-right" role="img" aria-label="Olive branch and open cream jar"></div>
<h2 class="abs sec-head" style="top:640px">Our <em>Products</em></h2>
<div class="abs sec-line" style="top:693px"></div>
<div class="abs sec-notch" style="top:694px"></div>

<div class="abs arrow prev"><svg width="16" height="16" viewBox="0 0 16 16"><path d="M10 2L4 8l6 6" fill="none" stroke="#fff" stroke-width="2"/></svg></div>
<div class="abs arrow next"><svg width="18" height="16" viewBox="0 0 18 16"><path d="M2 8h13M9 2l6 6-6 6" fill="none" stroke="#fff" stroke-width="2"/></svg></div>

<div class="abs product" style="left:117px">
  <div class="shot" role="img" aria-label="Gold cream jar" style="width:140px;background:radial-gradient(ellipse 62px 48px at 50% 55%,#e8cf6e 0%,#f0e2a8 55%,rgba(255,255,255,0) 100%)"></div>
  <p>Lorem ipsum dolor<br>sit amet consectetuer</p>
  <div class="price">$375,00<span class="cart"><svg width="18" height="16" viewBox="0 0 16 14"><path d="M0 1h3l2 8h9l2-6H4" fill="none" stroke="#fff" stroke-width="1.6"/><circle cx="6" cy="12" r="1.4" fill="#fff"/><circle cx="13" cy="12" r="1.4" fill="#fff"/></svg></span></div>
</div>
<div class="abs product" style="left:376px">
  <div class="shot" role="img" aria-label="Grey cream tube" style="width:70px;background:radial-gradient(ellipse 24px 72px at 50% 50%,#6c6c6c 0%,#9a9a9a 60%,rgba(255,255,255,0) 100%)"></div>
  <p>Lorem ipsum dolor<br>sit amet consectetuer</p>
  <div class="price">$145,00<span class="cart"><svg width="18" height="16" viewBox="0 0 16 14"><path d="M0 1h3l2 8h9l2-6H4" fill="none" stroke="#fff" stroke-width="1.6"/><circle cx="6" cy="12" r="1.4" fill="#fff"/><circle cx="13" cy="12" r="1.4" fill="#fff"/></svg></span></div>
</div>
<div class="abs product" style="left:637px">
  <div class="shot" role="img" aria-label="Gold serum pump bottle" style="width:50px;background:radial-gradient(ellipse 16px 74px at 50% 50%,#d9b22a 0%,#efd878 60%,rgba(255,255,255,0) 100%)"></div>
  <p>Lorem ipsum dolor<br>sit amet consectetuer</p>
  <div class="price">$375,00<span class="cart"><svg width="18" height="16" viewBox="0 0 16 14"><path d="M0 1h3l2 8h9l2-6H4" fill="none" stroke="#fff" stroke-width="1.6"/><circle cx="6" cy="12" r="1.4" fill="#fff"/><circle cx="13" cy="12" r="1.4" fill="#fff"/></svg></span></div>
</div>
<div class="abs product" style="left:898px">
  <div class="shot" role="img" aria-label="Blue glass dropper bottle" style="width:60px;background:radial-gradient(ellipse 22px 70px at 50% 55%,#1f4a9a 0%,#5d86c8 60%,rgba(255,255,255,0) 100%)"></div>
  <p>Lorem ipsum dolor<br>sit amet consectetuer</p>
  <div class="price">$375,00<span class="cart"><svg width="18" height="16" viewBox="0 0 16 14"><path d="M0 1h3l2 8h9l2-6H4" fill="none" stroke="#fff" stroke-width="1.6"/><circle cx="6" cy="12" r="1.4" fill="#fff"/><circle cx="13" cy="12" r="1.4" fill="#fff"/></svg></span></div>
</div>

<div class="abs consult" role="img" aria-label="Dermatologist in a white coat talking with a patient in a bright clinic"></div>
<div class="abs products-group" role="img" aria-label="Group of silver cosmetic bottles and jars"></div>
<h2 class="abs consult-title">Dermatologist Consultation</h2>
<p class="abs consult-text">Lorem ipsum dolor sit amet, consectetuer adipiscing elit, sed diam nonummy nibh euismod tincidunt ut laoreet dolore magna aliquam erat volutpat. Ut wisi enim ad minim veniam, quis nostrud exerci tation ullamcorper suscipit lobortis nisl ut aliquip ex ea commodo consequat. Duis autem vel eum iriure dolor in hendrerit.Lorem ipsum dolor sit amet, consectetuer adipiscing elit, sed diam nonummy nibh euismod tincidunt ut laoreet.</p>
<div class="abs btn-call"><svg width="24" height="24" viewBox="0 0 38 38"><path d="M11 6l6 6-3 4c2 4 4 6 8 8l4-3 6 6-4 5C18 32 6 20 6 10z" fill="#fff"/></svg>Call Us Today</div>

<h2 class="abs sec-head" style="top:1568px">Recent <em>Articles</em></h2>
<div class="abs sec-line" style="top:1619px"></div>
<div class="abs sec-notch" style="top:1620px"></div>

<article class="abs article" style="left:59px;top:1660px">
  <div class="abs pic" role="img" aria-label="Woman with red curly hair" style="background:radial-gradient(ellipse 70px 80px at 50% 50%,#b8481a 0%,#d77a45 60%,#f1d9c8 100%)"></div>
  <h3 class="abs">Lorem ipsum dolor sit amet</h3>
  <div class="abs meta"><span><svg width="14" height="14" viewBox="0 0 14 14"><circle cx="7" cy="7" r="6" fill="none" stroke="#222" stroke-width="1.5"/><path d="M7 3v4h3" fill="none" stroke="#222" stroke-width="1.5"/></svg>Aug 31, 2016</span><span><svg width="14" height="13" viewBox="0 0 14 13"><path d="M7 12L1 6a3 3 0 0 1 6-4 3 3 0 0 1 6 4z" fill="#222"/></svg>227</span><span><svg width="16" height="13" viewBox="0 0 16 13"><ellipse cx="8" cy="6" rx="7" ry="5" fill="none" stroke="#222" stroke-width="1.5"/></svg>2285</span></div>
  <p class="abs">Lorem ipsum dolor sit amet, sed dianummy nibh euismod tincidunt ut dolore. Lorem ipsum dolor ipsum dolor sit.</p>
  <div class="abs read-more">Read More</div>
</article>
<article class="abs article" style="left:643px;top:1660px">
  <div class="abs pic" role="img" aria-label="Woman relaxing at a spa with pink flowers" style="background:radial-gradient(ellipse 80px 60px at 60% 60%,#d9a283 0%,#f0d4c4 60%,#f7ece6 100%)"></div>
  <h3 class="abs">Lorem ipsum dolor sit amet</h3>
  <div class="abs meta"><span><svg width="14" height="14" viewBox="0 0 14 14"><circle cx="7" cy="7" r="6" fill="none" stroke="#222" stroke-width="1.5"/><path d="M7 3v4h3" fill="none" stroke="#222" stroke-width="1.5"/></svg>Aug 31, 2016</span><span><svg width="14" height="13" viewBox="0 0 14 13"><path d="M7 12L1 6a3 3 0 0 1 6-4 3 3 0 0 1 6 4z" fill="#222"/></svg>227</span><span><svg width="16" height="13" viewBox="0 0 16 13"><ellipse cx="8" cy="6" rx="7" ry="5" fill="none" stroke="#222" stroke-width="1.5"/></svg>2285</span></div>
  <p class="abs">Lorem ipsum dolor sit amet, sed dianummy nibh euismod tincidunt ut dolore. Lorem ipsum dolor ipsum dolor sit.</p>
  <div class="abs read-more">Read More</div>
</article>
<article class="abs article" style="left:59px;top:1881px">
  <div class="abs pic" role="img" aria-label="Smiling blonde woman touching her face" style="background:radial-gradient(ellipse 70px 80px at 50% 50%,#f2d2b6 0%,#e8c98c 60%,#f5ead2 100%)"></div>
  <h3 class="abs">Lorem ipsum dolor sit amet</h3>
  <div class="abs meta"><span><svg width="14" height="14" viewBox="0 0 14 14"><circle cx="7" cy="7" r="6" fill="none" stroke="#222" stroke-width="1.5"/><path d="M7 3v4h3" fill="none" stroke="#222" stroke-width="1.5"/></svg>Aug 31, 2016</span><span><svg width="14" height="13" viewBox="0 0 14 13"><path d="M7 12L1 6a3 3 0 0 1 6-4 3 3 0 0 1 6 4z" fill="#222"/></svg>227</span><span><svg width="16" height="13" viewBox="0 0 16 13"><ellipse cx="8" cy="6" rx="7" ry="5" fill="none" stroke="#222" stroke-width="1.5"/></svg>2285</span></div>
  <p class="abs">Lorem ipsum dolor sit amet, sed dianummy nibh euismod tincidunt ut dolore. Lorem ipsum dolor ipsum dolor sit.</p>
  <div class="abs read-more">Read More</div>
</article>
<article class="abs article" style="left:643px;top:1881px">
  <div class="abs pic" role="img" aria-label="Smiling dark-haired woman" style="background:radial-gradient(ellipse 60px 75px at 55% 50%,#e4c8b4 0%,#9a7a66 55%,#2e221c 100%)"></div>
  <h3 class="abs">Lorem ipsum dolor sit amet</h3>
  <div class="abs meta"><span><svg width="14" height="14" viewBox="0 0 14 14"><circle cx="7" cy="7" r="6" fill="none" stroke="#222" stroke-width="1.5"/><path d="M7 3v4h3" fill="none" stroke="#222" stroke-width="1.5"/></svg>Aug 31, 2016</span><span><svg width="14" height="13" viewBox="0 0 14 13"><path d="M7 12L1 6a3 3 0 0 1 6-4 3 3 0 0 1 6 4z" fill="#222"/></svg>227</span><span><svg width="16" height="13" viewBox="0 0 16 13"><ellipse cx="8" cy="6" rx="7" ry="5" fill="none" stroke="#222" stroke-width="1.5"/></svg>2285</span></div>
  <p class="abs">Lorem ipsum dolor sit amet, sed dianummy nibh euismod tincidunt ut dolore. Lorem ipsum dolor ipsum dolor sit.</p>
  <div class="abs read-more">Read More</div>
</article>

<div class="abs newsletter"></div>
<div class="abs nl-icon"><svg width="24" height="20" viewBox="0 0 24 20"><path d="M2 8l10-6 10 6v10H2z" fill="none" stroke="#222" stroke-width="2"/><path d="M2 8l10 6 10-6" fill="none" stroke="#222" stroke-width="2"/></svg></div>
<div class="abs nl-title">Join Our Newsletter!</div>
<div class="abs nl-sub">Be the first one to know about our new Offers</div>
<div class="abs nl-input">Enter Your Email Here</div>
<div class="abs nl-btn">SUBSCRIBE</div>

<footer class="abs footer"></footer>
<h4 class="abs f-head" style="left:62px">Our Philosophy</h4>
<div class="abs f-rule" style="left:62px;width:350px"></div>
<p class="abs philosophy">Lorem ipsum dolor sit amet, consectetuer adipisemy nibh euismod tincidunt utre magmi aliquam erat volutpat. Ut wisi enim ad minim veniam quis nostrutation ullaeipit lobortisi nisl ut aliquip nibh euismod tincidunt utre magmi aliquam erat volutpat .ipsum dolor sit amet, consectetuer adipisemy nibh euismod tincidunt utreipsum dolor.</p>

<h4 class="abs f-head" style="left:484px">Quick Links</h4>
<div class="abs f-rule" style="left:484px;width:346px"></div>
<ul class="abs links" style="left:484px"><li>Home</li><li>Face</li><li>Body</li><li>Hair Care</li><li>Skin Concerns</li></ul>
<ul class="abs links" style="left:627px"><li>Dermatologist Consultation</li><li>Library</li><li>Contact Us</li><li>Our Doctors</li><li>Customer Care</li></ul>

<h4 class="abs f-head" style="left:900px">Contact Details</h4>
<div class="abs f-rule" style="left:900px;width:238px"></div>
<div class="abs cinfo" style="top:2258px"><svg width="14" height="18" viewBox="0 0 14 18"><path d="M7 17S1 10 1 6a6 6 0 0 1 12 0c0 4-6 11-6 11z" fill="var(--gold)"/><circle cx="7" cy="6" r="2" fill="#141414"/></svg><div><b>Velour Skinhaus</b><br>123 PG Duis Aute Irur Dolore<br>Srephenderit Amit In Voluptate</div></div>
<div class="abs cinfo" style="top:2330px"><svg width="16" height="16" viewBox="0 0 38 38"><path d="M11 6l6 6-3 4c2 4 4 6 8 8l4-3 6 6-4 5C18 32 6 20 6 10z" fill="var(--gold)"/></svg><b>+123-456-789</b></div>
<div class="abs cinfo" style="top:2368px"><svg width="16" height="12" viewBox="0 0 16 12"><rect x="1" y="1" width="14" height="10" fill="none" stroke="var(--gold)" stroke-width="1.5"/><path d="M1 1l7 6 7-6" fill="none" stroke="var(--gold)" stroke-width="1.5"/></svg>info@velourskinhaus.com</div>

<div class="abs f-bottom"></div>
<div class="abs copyright">Copyright © 2016 Velour Skinhaus. All Rights Reserved.</div>
<div class="abs social"><i></i><i></i><i></i><i></i></div>
<div class="abs accept">We Accept :<i></i><i></i><i></i><i></i><i></i></div>

</body>
</html>
```